Crestline Plaque & Medal Unique Business Card Design

Recently selected a new logo design and waiting to recieve print files. I've attached image for your review. We are a trophies and awards company that provides engraving on trophies, plaques, name plates, name tags, desk sets, medals, acrylics, and signage.

We are located in Monroe, Louisiana and provide this service with computerized & laser engraving equipment.

Target Market(s)

Corporate, Sport, Church, and Special Events

Industry/Entity Type

Business

Contact Information for Business Card

I'd like to see the following list on the card: Trophies, Plaques, Name Plates, Name Tags, Desk Sets, Medals, Certificates... this is accomplished with Computerized & Laser Engraving

Colors
0555a3
ec1f27
ffffff

Requirements
Must have
• I like either single or double sided. If a design can be created with a frosted card stock I'd consider single. Must be Red, White, and Blue. Dwight Palmer - Owner, 412 W 8th Ave, Monroe, La 71208 office 318-555-0148 fax 318-555-0163 email: info@crestlineplaquemedal.example, and website: www.crestlineplaquemedal.example

```html
<!DOCTYPE html>
<html lang="en">
<head>
<meta charset="utf-8">
<title>Crestline Plaque &amp; Medal — Business Card</title>
<link rel="stylesheet" href="https://fonts.googleapis.com/css2?family=Montserrat:wght@700&family=Mulish:wght@400&family=Great+Vibes&display=swap">
<style>
  :root {
    --brand-blue: #0555a3;
    --navy: #1c2a86;
    --navy-deep: #16217a;
    --brand-red: #ec1f27;
    --script-red: #d8262c;
    --white: #ffffff;
    --frost: #eef1f4;
    --page-bg: #e4e4e2;
    --text-light: #e6e9f5;
  }
  html, body {
    margin: 0;
    width: 1200px;
    height: 970px;
    overflow: hidden;
    background: var(--page-bg);
  }
  .card {
    position: absolute;
    left: 60px;
    top: 185px;
    width: 1080px;
    height: 600px;
    background: var(--frost);
    box-shadow: 0 6px 24px rgba(0,0,0,0.18);
    overflow: hidden;
    font-family: "Mulish", "Helvetica Neue", Arial, sans-serif;
  }
  .card__top {
    position: absolute;
    inset: 0 0 auto 0;
    height: 240px;
    background: linear-gradient(180deg, #f4f5f6 0%, #e9eef3 100%);
  }
  .brand {
    position: absolute;
    left: 0;
    right: 0;
    top: 92px;
    display: flex;
    justify-content: center;
    align-items: center;
    gap: 16px;
  }
  .brand__dot {
    width: 22px;
    height: 22px;
    border-radius: 50%;
    background: var(--navy);
  }
  .brand__name {
    font-family: "Montserrat", Arial, sans-serif;
    font-weight: 700;
    font-size: 52px;
    color: var(--navy);
    letter-spacing: 0.5px;
  }
  .divider {
    position: absolute;
    left: 0;
    right: 0;
    top: 240px;
    height: 3px;
    background: var(--navy);
  }
  .divider--second { top: 246px; height: 2px; }
  .card__band {
    position: absolute;
    left: 0;
    right: 0;
    top: 252px;
    bottom: 0;
    background: linear-gradient(90deg, var(--navy) 0%, #34478f 45%, var(--navy-deep) 70%, var(--navy) 100%);
  }
  .person {
    position: absolute;
    left: 62px;
    top: 18px;
  }
  .person__name {
    font-family: "Great Vibes", cursive;
    font-size: 50px;
    color: var(--script-red);
    line-height: 1;
    margin: 0;
  }
  .person__title {
    font-size: 22px;
    color: var(--text-light);
    margin: 12px 0 0;
  }
  .contact {
    position: absolute;
    left: 62px;
    top: 155px;
    margin: 0;
    padding: 0;
    list-style: none;
    font-size: 26px;
    color: var(--text-light);
  }
  .contact__item {
    display: flex;
    align-items: flex-start;
    gap: 24px;
    line-height: 28px;
    margin-bottom: 8px;
  }
  .contact__icon { width: 24px; height: 24px; flex: none; margin-top: 2px; }
  .services {
    position: absolute;
    left: 630px;
    top: 48px;
  }
  .services__tagline {
    font-family: "Great Vibes", cursive;
    font-size: 34px;
    color: var(--script-red);
    margin: 0 0 28px;
  }
  .services__list {
    list-style: none;
    margin: 0;
    padding: 0;
    font-size: 26px;
    color: var(--text-light);
  }
  .services__list li {
    display: flex;
    align-items: center;
    gap: 18px;
    line-height: 32px;
  }
  .services__star { width: 16px; height: 16px; flex: none; }
</style>
</head>
<body>
  <article class="card">
    <header class="card__top">
      <div class="brand">
        <span class="brand__dot"></span>
        <span class="brand__name">Crestline Plaque &amp; Medal</span>
      </div>
    </header>
    <div class="divider"></div>
    <div class="divider divider--second"></div>

    <section class="card__band">
      <div class="person">
        <h1 class="person__name">Dwight Palmer</h1>
        <p class="person__title">Managing Director</p>
      </div>

      <ul class="contact">
        <li class="contact__item">
          <svg class="contact__icon" viewBox="0 0 24 24"><path fill="#ec1f27" d="M6.6 10.8a15.1 15.1 0 0 0 6.6 6.6l2.2-2.2a1 1 0 0 1 1-.25 11.4 11.4 0 0 0 3.6.57 1 1 0 0 1 1 1V20a1 1 0 0 1-1 1A17 17 0 0 1 3 4a1 1 0 0 1 1-1h3.5a1 1 0 0 1 1 1c0 1.25.2 2.45.57 3.57a1 1 0 0 1-.25 1z"/></svg>
          <span>318-555-0148</span>
        </li>
        <li class="contact__item">
          <svg class="contact__icon" viewBox="0 0 24 24"><rect x="2" y="6" width="20" height="13" fill="#ec1f27"/><path d="M2 6l10 7 10-7" fill="none" stroke="#1c2a86" stroke-width="1.5"/></svg>
          <span>info@crestlineplaquemedal.example</span>
        </li>
        <li class="contact__item">
          <svg class="contact__icon" viewBox="0 0 24 24"><circle cx="12" cy="12" r="10" fill="#ec1f27"/><path d="M2 12h20M12 2c3 3 3 17 0 20M12 2c-3 3-3 17 0 20" fill="none" stroke="#1c2a86" stroke-width="1.3"/></svg>
          <span>www.crestlineplaquemedal.example</span>
        </li>
        <li class="contact__item">
          <svg class="contact__icon" viewBox="0 0 24 24"><path fill="#ec1f27" d="M12 2a7 7 0 0 0-7 7c0 5 7 13 7 13s7-8 7-13a7 7 0 0 0-7-7zm0 9.5A2.5 2.5 0 1 1 12 6.5a2.5 2.5 0 0 1 0 5z"/></svg>
          <span>412 W 8th Ave<br>Monroe, La 71208</span>
        </li>
      </ul>

      <div class="services">
        <p class="services__tagline">computerize &amp; laser engraving</p>
        <ul class="services__list">
          <li><svg class="services__star" viewBox="0 0 24 24"><path fill="#ec1f27" d="M12 2l2.9 6.9 7.1.6-5.4 4.7 1.7 7.3L12 17.6 5.7 21.5l1.7-7.3L2 9.5l7.1-.6z"/></svg>plaques</li>
          <li><svg class="services__star" viewBox="0 0 24 24"><path fill="#ec1f27" d="M12 2l2.9 6.9 7.1.6-5.4 4.7 1.7 7.3L12 17.6 5.7 21.5l1.7-7.3L2 9.5l7.1-.6z"/></svg>name plates</li>
          <li><svg class="services__star" viewBox="0 0 24 24"><path fill="#ec1f27" d="M12 2l2.9 6.9 7.1.6-5.4 4.7 1.7 7.3L12 17.6 5.7 21.5l1.7-7.3L2 9.5l7.1-.6z"/></svg>name tags</li>
          <li><svg class="services__star" viewBox="0 0 24 24"><path fill="#ec1f27" d="M12 2l2.9 6.9 7.1.6-5.4 4.7 1.7 7.3L12 17.6 5.7 21.5l1.7-7.3L2 9.5l7.1-.6z"/></svg>desk sets</li>
          <li><svg class="services__star" viewBox="0 0 24 24"><path fill="#ec1f27" d="M12 2l2.9 6.9 7.1.6-5.4 4.7 1.7 7.3L12 17.6 5.7 21.5l1.7-7.3L2 9.5l7.1-.6z"/></svg>medals</li>
          <li><svg class="services__star" viewBox="0 0 24 24"><path fill="#ec1f27" d="M12 2l2.9 6.9 7.1.6-5.4 4.7 1.7 7.3L12 17.6 5.7 21.5l1.7-7.3L2 9.5l7.1-.6z"/></svg>acrylics, and signage</li>
        </ul>
      </div>
    </section>
  </article>
</body>
</html>
```